Velmarotix - world unique technology for better life - please let them know who am i at first sight

We need a new business card for company which is a provider of unique crystal based technology suitable for all living being. For more information and final design you can use our brochure (our colours are black and blue from brochure).
We use Verdana font

Industry/Entity Type

Business

Contact Information for Business Card

regular dimension

Font styles to use
Other font styles liked:
• Verdana

Requirements
Must have
• Logo
• name
• function/position
• phone
• mobile
• e-mail
• adress
Nice to have
• inovative design (technology directed)

```html
<!DOCTYPE html>
<html lang="en">
<head>
<meta charset="utf-8">
<title>Velmarotix – Business Card</title>
<link rel="stylesheet" href="https://fonts.googleapis.com/css2?family=Lexend:wght@300;400;500&display=swap">
<style>
  :root {
    --page: #e8ebee;
    --brand-blue: #29a8e0;
    --brand-black: #16181b;
    --panel-white: #ffffff;
    --panel-grey: #b9bcc0;
    --ink-light: #ffffff;
    --card-shadow: rgba(20, 40, 60, 0.18);
  }
  * { box-sizing: border-box; margin: 0; padding: 0; }
  html, body {
    width: 1200px; height: 900px; overflow: hidden;
    background: var(--page);
    font-family: Verdana, "Lexend", sans-serif;
  }
  .canvas {
    width: 1200px; height: 900px;
    display: flex; flex-direction: column; align-items: center; justify-content: center;
    gap: 48px;
  }
  .card {
    position: relative;
    width: 640px; height: 366px;
    border-radius: 38px;
    background: var(--brand-blue);
    overflow: hidden;
    box-shadow: 0 10px 28px var(--card-shadow);
  }
  .card-front__shape { position: absolute; inset: 0; }
  .identity {
    position: absolute; left: 40px; top: 34px; color: var(--ink-light);
  }
  .identity__name { font-size: 20px; font-weight: 500; }
  .identity__role { font-size: 14px; font-weight: 300; margin-top: 4px; }
  .contacts {
    position: absolute; left: 40px; top: 160px; list-style: none; color: var(--ink-light);
    font-size: 13px; font-weight: 300;
  }
  .contacts__item { display: flex; align-items: center; gap: 10px; margin-bottom: 10px; }
  .contacts__icon { width: 20px; height: 20px; flex: none; }
  .brand {
    position: absolute; display: flex; align-items: center; gap: 12px;
    font-weight: 400; letter-spacing: 1.5px;
  }
  .brand__dot { border-radius: 50%; flex: none; }
  .brand--front { left: 336px; top: 150px; color: var(--brand-blue); font-size: 24px; }
  .brand--front .brand__dot { width: 36px; height: 36px; background: var(--brand-blue); }
  .address {
    position: absolute; left: 384px; top: 200px;
    color: var(--brand-black); font-size: 12px; font-weight: 300; line-height: 1.5;
    font-style: normal;
  }
  .brand--back { left: 50%; top: 50%; transform: translate(-50%, -50%); color: var(--ink-light); font-size: 34px; }
  .brand--back .brand__dot { width: 50px; height: 50px; background: var(--brand-black); }
</style>
</head>
<body>
<main class="canvas">

  <section class="card card-front" aria-label="Business card, front">
    <svg class="card-front__shape" viewBox="0 0 640 366" aria-hidden="true">
      <rect x="262" y="6" width="440" height="392" rx="118" fill="var(--panel-grey)"/>
      <rect x="292" y="22" width="420" height="370" rx="108" fill="var(--panel-white)"/>
    </svg>

    <div class="identity">
      <p class="identity__name">Dorian Falkenreth</p>
      <p class="identity__role">Director</p>
    </div>

    <ul class="contacts">
      <li class="contacts__item">
        <svg class="contacts__icon" viewBox="0 0 22 22" aria-hidden="true">
          <circle cx="11" cy="11" r="11" fill="var(--ink-light)"/>
          <path d="M7.5 6.5c.6-.5 1.3-.4 1.6.1l1 1.6c.3.5.1 1-.3 1.3l-.6.4c.5 1.2 1.5 2.2 2.7 2.7l.4-.6c.3-.4.8-.6 1.3-.3l1.6 1c.5.3.6 1 .1 1.6-.8.9-2 1.2-3.1.7-2.3-1-4.2-2.9-5.2-5.2-.5-1.1-.2-2.3.5-3.3z" fill="var(--brand-blue)"/>
        </svg>
        <span>014 672 3958</span>
      </li>
      <li class="contacts__item">
        <svg class="contacts__icon" viewBox="0 0 22 22" aria-hidden="true">
          <circle cx="11" cy="11" r="11" fill="var(--ink-light)"/>
          <rect x="7.5" y="5" width="7" height="12" rx="1.4" fill="var(--brand-blue)"/>
          <rect x="8.7" y="6.6" width="4.6" height="7.4" fill="var(--ink-light)"/>
        </svg>
        <span>014 672 3958</span>
      </li>
      <li class="contacts__item">
        <svg class="contacts__icon" viewBox="0 0 22 22" aria-hidden="true">
          <circle cx="11" cy="11" r="11" fill="var(--ink-light)"/>
          <rect x="5.5" y="7" width="11" height="8" rx="1" fill="var(--brand-blue)"/>
          <path d="M6 7.6l5 4 5-4" fill="none" stroke="var(--ink-light)" stroke-width="1.2"/>
        </svg>
        <span>dorian@velmarotix.com</span>
      </li>
    </ul>

    <div class="brand brand--front">
      <span class="brand__dot"></span>
      <span class="brand__name">VELMAROTIX</span>
    </div>

    <address class="address">
      27 Harrowgate Lane<br>
      Brenton 40512
    </address>
  </section>

  <section class="card card-back" aria-label="Business card, back">
    <div class="brand brand--back">
      <span class="brand__dot"></span>
      <span class="brand__name">VELMAROTIX</span>
    </div>
  </section>

</main>
</body>
</html>
```